Maple Lantern Productions web site

I need to build a website for a new company I am launching next month. Maple Lantern Productions is a company based in New England that provides sound, lighting, and audio visual services to weddings, corporate, and any other cusomer base looking for quality service for a fair price. Looking for somebody to do a full site not just the image files. I am looking to keep the colors of my logo (orange and black) and possibly grey and white. I am looking to build my site very similar to brightvaleevents.example, which is owned by a friend of mine. I like how he has the big pictures that load in to the site and the basic menu items. I'll need a gallery of photos. The designs should communicate quality, value and trust.
My website address is maplelanternco.example.
Updates

Hi and thanks to everyone for posting such great ideas for our new design.I have some items that I'd like to ask you all to focus on in your revisions.I like how http://www.brightvaleevents.example/ website has five or six high res pictures that change in a slideshow format with a caption that loads in for each one for the different types of services. Try and capture pics like these and with teh same headings as he has. The basic menu designs have been interesting.I am more fond of the menus that are more white with some orange as I dont want it to be too dark. I'm curious to see how your galleries will work and if i'll be able to edit the pages myself? I have some more info on the company for you to fill in:website address is ciderhouseco.comemail: info@ciderhouseco.comaddress: Maple Lantern Productions57 Littlefield StreetAvon, MA 02417"New England's finest DJ's, lighting and sound, video and more. Creating memories one perfect event at a time."Put this under the loading pictures as a tagline.About Cider HouseCider House Productions is a collection of New England's finest talent, ready to make your next event the one you've dreamed of. We have the skills and expertise to deliver your vision of your perfect event. From elegant weddings to themed mitzvah's, corporate av, videography and detail lighting, we offer all of the elements to make your event a success. Added Wednesday, March 1, 2017

Designer's Please also make sure that your design flows well on any device it is being viewed on as well. Thanks. Added Wednesday, March 1, 2017

Project Deadline Extended Reason: Hello designerThank you all very much for your hard work on our project. Im sorry but i need to extend the date of my project. Our parent conpany Rook Nine Prodactions sponsors Bay Youth Assemblies and we are currently at their leadership conference on the Cape. I will be back in on Monday and with your help will get this finished by Thursday the 16th. Thanks Added Thursday, March 9, 2017

Project Deadline Extended Reason: One of the designers is not responding so I now have to make revisions with other designers. I hope to get this website done over the weekends so please get your revisions as soon as possible. Thank you. I am also upgrading the budget another $75 to hopefully get some more interest on my project. Added Wednesday, March 15, 2017

Target Market(s)

Wedding - Corporate -

Industry/Entity Type

It Company

Coding

Coded - Design and coding required

Number of Pages Required

5+ page

Font styles to use
Sans Serif

Requirements
Must have
• Photo Gallery - I want to be able to edit it myself
Nice to have
• I like the look of my friends website brightvaleevents.example

```html
<!DOCTYPE html>
<html lang="en">
<head>
<meta charset="utf-8">
<title>Maple Lantern Productions</title>
<link href="https://fonts.googleapis.com/css2?family=Questrial&display=swap" rel="stylesheet">
<style>
:root{
  --orange:#f26a21;
  --ink:#2b2b2b;
  --text:#555;
  --muted:#8a8a8a;
  --line:#d9d9d9;
  --soft:#f1f1f1;
  --band:#bdbdbd;
  --white:#fff;
}
*{margin:0;padding:0;box-sizing:border-box}
html,body{width:1200px;height:2871px;overflow:hidden}
body{font-family:"Questrial",sans-serif;color:var(--text);background:var(--white);position:relative}
.abs{position:absolute}
.photo{position:absolute}

/* hero */
.hero{left:0;top:0;width:1200px;height:469px;background:radial-gradient(ellipse at 45% 35%,#c98a7a 0%,#8a5561 30%,#4b2f3a 60%,#e9e5ea 92%)}
.hero-fade{left:0;top:330px;width:1200px;height:139px;background:linear-gradient(180deg,rgba(255,255,255,0),rgba(238,236,240,.9))}
.nav{left:249px;top:10px;width:702px;height:40px;background:var(--white);display:flex;align-items:center;justify-content:space-between;padding-left:10px}
.brand{display:flex;align-items:center;gap:7px;font-size:13px;color:var(--ink);letter-spacing:.5px}
.brand-dot{width:22px;height:22px;border-radius:50%;background:var(--orange)}
.menu{display:flex;height:100%;font-size:11.5px;color:var(--ink)}
.menu a{display:flex;align-items:center;padding:0 9px;text-decoration:none;color:inherit}
.menu a.active{background:var(--orange);color:var(--white)}
.caption{left:402px;top:245px;width:390px;height:163px;background:rgba(70,60,65,.72);border:1px solid rgba(255,255,255,.35);outline:1px solid rgba(255,255,255,.5);outline-offset:-7px;text-align:center;color:var(--white)}
.caption h1{font-weight:400;font-size:27px;margin-top:14px;line-height:32px}
.caption .rule{width:340px;height:1px;background:rgba(255,255,255,.5);margin:4px auto 7px}
.caption p{font-size:11px;line-height:16px;padding:0 16px;white-space:nowrap}
.btn-ghost{display:inline-block;margin-top:15px;width:126px;height:33px;line-height:31px;border:1px solid var(--white);font-size:13px}
.dots{left:583px;top:448px;display:flex;gap:4px}
.dots i{width:7px;height:7px;border-radius:50%;background:rgba(255,255,255,.6)}
.dots i.on{background:var(--white);box-shadow:0 0 0 1px #999}

/* headings */
.sec-title{left:0;width:1200px;text-align:center;font-size:27px;color:var(--ink);font-weight:400}
.sec-rule{left:321px;width:558px;height:1px;background:var(--line)}
.chev{left:593px;width:14px;height:8px}

.intro-text{left:249px;top:572px;width:702px;text-align:center;font-size:9.5px;line-height:20px;color:var(--muted)}
.btn-grey{left:505px;top:653px;width:190px;height:32px;background:#b4b4b4;color:var(--white);font-size:12px;text-align:center;line-height:32px}

/* services */
.services{left:0;top:723px;width:1200px;height:263px;background:linear-gradient(90deg,#3b3532 0%,#5a4a44 35%,#2b2523 60%,#4a3d3a 100%)}
.services .sec-title{color:var(--white);top:20px}
.services .sec-rule{background:rgba(255,255,255,.3);top:65px}
.svc{top:113px;width:150px;text-align:center;color:var(--white)}
.svc-icon{width:42px;height:42px;border-radius:50%;border:1px solid rgba(255,255,255,.8);margin:0 auto 14px;display:flex;align-items:center;justify-content:center}
.svc h3{font-weight:400;font-size:12px;margin-bottom:5px}
.svc p{font-size:8.5px;line-height:12px;color:#ddd}

/* cards */
.card{width:224px;height:289px;border:1px solid var(--line);background:var(--white)}
.card .photo{left:0;top:0;width:222px;height:172px;position:relative}
.card h4{font-weight:400;color:var(--orange);font-size:15px;text-align:center;margin-top:9px}
.card .crule{height:1px;background:var(--line);margin:6px 0 8px}
.card p{font-size:8.2px;line-height:13px;text-align:center;padding:0 10px;color:var(--muted)}
.card-foot{position:absolute;left:0;bottom:0;width:100%;height:22px;border-top:1px solid var(--line);display:flex;font-size:9.5px;color:var(--ink)}
.card-foot span{flex:1;display:flex;align-items:center;gap:3px;padding-left:22px}
.card-foot span+span{border-left:1px solid var(--line)}

/* gallery */
.tabs{top:1786px;left:321px;display:flex;gap:2px;font-size:9.5px;color:var(--text)}
.tabs span{background:#efefef;padding:0 7px;height:25px;line-height:25px}
.tabs span.on{background:var(--orange);color:var(--white)}
.tile{width:164px;height:164px;border:2px solid #444}
.viewall{inset:0;background:rgba(90,90,90,.8);display:flex;flex-direction:column;align-items:center;justify-content:center;color:var(--white);font-size:13px}
.viewall i{width:80px;height:1px;background:rgba(255,255,255,.7);margin-top:6px}

/* testimonial */
.testi{left:0;top:2216px;width:1200px;height:301px;background:var(--soft)}
.avatar{left:557px;top:29px;width:86px;height:86px;border-radius:50%;border:3px solid var(--white);background:linear-gradient(160deg,#c7a58e,#6d5a52);box-shadow:0 1px 4px rgba(0,0,0,.2)}
.stars{left:0;top:124px;width:1200px;text-align:center;line-height:0}
.quote{left:290px;top:150px;width:620px;text-align:center;font-style:italic;font-size:10px;line-height:15px;color:var(--muted)}
.author{left:0;top:204px;width:1200px;text-align:center;font-size:10px;color:var(--ink)}
.author b{color:var(--orange);font-weight:400}
.pager{left:420px;top:255px;width:360px;height:10px}

/* availability */
.avail{left:0;top:2517px;width:1200px;height:52px;background:var(--band)}
.select{top:14px;width:150px;height:25px;background:var(--white);border:1px solid #ccc;font-size:9.5px;color:var(--muted);line-height:23px;padding-left:8px}
.select svg{position:absolute;right:7px;top:9px}
.check{top:13px;left:783px;width:150px;height:27px;background:var(--orange);color:var(--white);font-size:10px;text-align:center;line-height:27px}

/* footer */
.social{left:543px;top:2585px;display:flex;gap:5px}
.social i{width:18px;height:18px;border-radius:3px;background:#8c8c8c}
.social i:first-child{background:var(--orange)}
.foot-col{top:2661px;width:150px;font-size:10px;color:var(--ink)}
.foot-col h5{font-weight:400;color:var(--orange);font-size:12px;margin-bottom:7px}
.foot-col li{list-style:none;height:21.5px}
.copyright{left:0;top:2840px;width:1200px;text-align:center;font-size:9.5px;color:var(--ink)}
</style>
</head>
<body>

<!-- Hero -->
<div class="abs hero photo" role="img" aria-label="Bride and groom dancing on a dance floor surrounded by guests"></div>
<div class="abs hero-fade"></div>
<header class="abs nav">
  <div class="brand"><span class="brand-dot"></span>Maple Lantern</div>
  <nav class="menu">
    <a class="active">Home</a><a>About Us</a><a>Our Services</a><a>Blog</a><a>Contact Us</a>
  </nav>
</header>
<div class="abs caption">
  <h1>Beautiful Wedding Events</h1>
  <div class="rule"></div>
  <p>Lorem Ipsum is simply dummy text of the printing and typesetting<br>industry. Lorem Ipsum has beenLorem Ipsum is simply dummy text</p>
  <span class="btn-ghost">Contact US</span>
</div>
<div class="abs dots"><i></i><i class="on"></i><i></i><i></i></div>

<!-- Intro -->
<h2 class="abs sec-title" style="top:497px">Maple Lantern are Experts in All Type of Events</h2>
<div class="abs sec-rule" style="top:547px"></div>
<svg class="abs chev" style="top:543px" viewBox="0 0 14 8"><polyline points="1,1 7,7 13,1" fill="none" stroke="#999" stroke-width="1.2"/></svg>
<p class="abs intro-text">Lorem Ipsum is simply dummy text of the printing and typesetting industry. Lorem Ipsum has been the industry's standard dummy text ever since the 1500s, when an unknown printer took a galley of type and scrambled it to make a type specimen book. It has survived not only five centuries, but also the leap into electronic typesetting, remaining essentially unchanged. It was popularised in the</p>
<div class="abs btn-grey">How can we help you ?</div>

<!-- Services -->
<section class="abs services photo" role="img" aria-label="Guests raising glasses in a toast at a dim reception">
  <h2 class="abs sec-title">Our Services</h2>
  <div class="abs sec-rule"></div>
  <svg class="abs chev" style="top:61px" viewBox="0 0 14 8"><polyline points="1,1 7,7 13,1" fill="none" stroke="#ccc" stroke-width="1.2"/></svg>
  <div class="abs svc" style="left:250px">
    <div class="svc-icon"><svg width="18" height="16" viewBox="0 0 18 16"><rect x="1" y="4" width="16" height="11" rx="1.5" fill="#fff"/><rect x="6" y="1" width="6" height="4" fill="none" stroke="#fff" stroke-width="1.5"/></svg></div>
    <h3>Corporate Events</h3><p>Lorem Ipsum is simply dummy text of the printing and typesetting industry. Lorem Ipsum has been the industry's</p>
  </div>
  <div class="abs svc" style="left:432px">
    <div class="svc-icon"><svg width="16" height="18" viewBox="0 0 16 18"><path d="M11 1v11a3 3 0 1 1-2-2.8V1z" fill="#fff"/></svg></div>
    <h3>Music Concert</h3><p>Lorem Ipsum is simply dummy text of the printing and typesetting industry. Lorem Ipsum has been the industry's</p>
  </div>
  <div class="abs svc" style="left:614px">
    <div class="svc-icon"><svg width="22" height="14" viewBox="0 0 22 14"><circle cx="8" cy="7" r="5.5" fill="none" stroke="#fff" stroke-width="2"/><circle cx="14" cy="7" r="5.5" fill="none" stroke="#fff" stroke-width="2"/></svg></div>
    <h3>Wedding Plane</h3><p>Lorem Ipsum is simply dummy text of the printing and typesetting industry. Lorem Ipsum has been the industry's</p>
  </div>
  <div class="abs svc" style="left:800px">
    <div class="svc-icon"><svg width="22" height="16" viewBox="0 0 22 16"><polygon points="11,1 21,6 11,11 1,6" fill="#fff"/><path d="M5 8v4c3 3 9 3 12 0V8l-6 3z" fill="#fff"/></svg></div>
    <h3>School and Formal Events</h3><p>Lorem Ipsum is simply dummy text of the printing and typesetting industry. Lorem Ipsum has been the industry's</p>
  </div>
</section>

<!-- Recent work -->
<h2 class="abs sec-title" style="top:1011px">Recent Work</h2>
<div class="abs sec-rule" style="top:1057px"></div>
<svg class="abs chev" style="top:1053px" viewBox="0 0 14 8"><polyline points="1,1 7,7 13,1" fill="none" stroke="#999" stroke-width="1.2"/></svg>

<article class="abs card" style="left:249px;top:1099px">
  <div class="photo" role="img" aria-label="Audience seated at a corporate presentation" style="background:linear-gradient(160deg,#c9c3cf,#6a5a66 60%,#3a2e3a)"></div>
  <h4>Corporate Events</h4><div class="crule"></div>
  <p>Lorem Ipsum is simply dummy text of the printing and typesetting industry. Lorem Ipsum has been the industry's standard dummy text ever</p>
  <div class="card-foot"><span><svg width="10" height="8"><rect width="10" height="8" fill="#f26a21"/></svg>See Photo</span><span><svg width="7" height="10" viewBox="0 0 7 10"><path d="M3.5 0a3.5 3.5 0 0 1 3.5 3.5C7 6 3.5 10 3.5 10S0 6 0 3.5A3.5 3.5 0 0 1 3.5 0z" fill="#f26a21"/></svg>See Location</span></div>
</article>
<article class="abs card" style="left:488px;top:1099px">
  <div class="photo" role="img" aria-label="Bride and groom walking among wedding guests" style="background:linear-gradient(160deg,#c9b277,#8f7a4a 55%,#4d4430)"></div>
  <h4>Wedding Event</h4><div class="crule"></div>
  <p>Lorem Ipsum is simply dummy text of the printing and typesetting industry. Lorem Ipsum has been the industry's standard dummy text ever</p>
  <div class="card-foot"><span><svg width="10" height="8"><rect width="10" height="8" fill="#f26a21"/></svg>See Photo</span><span><svg width="7" height="10" viewBox="0 0 7 10"><path d="M3.5 0a3.5 3.5 0 0 1 3.5 3.5C7 6 3.5 10 3.5 10S0 6 0 3.5A3.5 3.5 0 0 1 3.5 0z" fill="#f26a21"/></svg>See Location</span></div>
</article>
<article class="abs card" style="left:727px;top:1099px">
  <div class="photo" role="img" aria-label="Friends dancing at a high school party" style="background:linear-gradient(160deg,#e6c58a,#b07a4a 50%,#3f6a75)"></div>
  <h4>High School Party</h4><div class="crule"></div>
  <p>Lorem Ipsum is simply dummy text of the printing and typesetting industry. Lorem Ipsum has been the industry's standard dummy text ever</p>
  <div class="card-foot"><span><svg width="10" height="8"><rect width="10" height="8" fill="#f26a21"/></svg>See Photo</span><span><svg width="7" height="10" viewBox="0 0 7 10"><path d="M3.5 0a3.5 3.5 0 0 1 3.5 3.5C7 6 3.5 10 3.5 10S0 6 0 3.5A3.5 3.5 0 0 1 3.5 0z" fill="#f26a21"/></svg>See Location</span></div>
</article>
<article class="abs card" style="left:249px;top:1405px">
  <div class="photo" role="img" aria-label="Concert crowd with raised hands under blue stage lights" style="background:linear-gradient(180deg,#9fd0f0,#3a78b8 45%,#0e1a30)"></div>
  <h4>Music Concert</h4><div class="crule"></div>
  <p>Lorem Ipsum is simply dummy text of the printing and typesetting industry. Lorem Ipsum has been the industry's standard dummy text ever</p>
  <div class="card-foot"><span><svg width="10" height="8"><rect width="10" height="8" fill="#f26a21"/></svg>See Photo</span><span><svg width="7" height="10" viewBox="0 0 7 10"><path d="M3.5 0a3.5 3.5 0 0 1 3.5 3.5C7 6 3.5 10 3.5 10S0 6 0 3.5A3.5 3.5 0 0 1 3.5 0z" fill="#f26a21"/></svg>See Location</span></div>
</article>
<article class="abs card" style="left:488px;top:1405px">
  <div class="photo" role="img" aria-label="Guests toasting with drinks at a celebration" style="background:linear-gradient(160deg,#6a3a24,#b06a3a 45%,#2a1610)"></div>
  <h4>Bar / Bal Mitzvahs</h4><div class="crule"></div>
  <p>Lorem Ipsum is simply dummy text of the printing and typesetting industry. Lorem Ipsum has been the industry's standard dummy text ever</p>
  <div class="card-foot"><span><svg width="10" height="8"><rect width="10" height="8" fill="#f26a21"/></svg>See Photo</span><span><svg width="7" height="10" viewBox="0 0 7 10"><path d="M3.5 0a3.5 3.5 0 0 1 3.5 3.5C7 6 3.5 10 3.5 10S0 6 0 3.5A3.5 3.5 0 0 1 3.5 0z" fill="#f26a21"/></svg>See Location</span></div>
</article>
<article class="abs card" style="left:727px;top:1405px">
  <div class="photo" role="img" aria-label="Children celebrating a birthday with balloons" style="background:linear-gradient(160deg,#6bb6e0,#e8c070 45%,#d4573a)"></div>
  <h4>Birthdays Party</h4><div class="crule"></div>
  <p>Lorem Ipsum is simply dummy text of the printing and typesetting industry. Lorem Ipsum has been the industry's standard dummy text ever</p>
  <div class="card-foot"><span><svg width="10" height="8"><rect width="10" height="8" fill="#f26a21"/></svg>See Photo</span><span><svg width="7" height="10" viewBox="0 0 7 10"><path d="M3.5 0a3.5 3.5 0 0 1 3.5 3.5C7 6 3.5 10 3.5 10S0 6 0 3.5A3.5 3.5 0 0 1 3.5 0z" fill="#f26a21"/></svg>See Location</span></div>
</article>

<!-- Gallery -->
<h2 class="abs sec-title" style="top:1719px">Photo Gallery</h2>
<div class="abs sec-rule" style="top:1764px"></div>
<svg class="abs chev" style="top:1760px" viewBox="0 0 14 8"><polyline points="1,1 7,7 13,1" fill="none" stroke="#999" stroke-width="1.2"/></svg>
<div class="abs tabs"><span class="on">All</span><span>Corporate Events</span><span>Wedding Events</span><span>Music Concert</span><span>Bar / Bal Mitzvahs</span><span>Birthday Party</span><span>High School Party</span></div>

<div class="abs tile photo" style="left:251px;top:1836px;background:linear-gradient(160deg,#3a5fb0,#9a4ab0 50%,#2a1a40)" role="img" aria-label="Party guests under colourful lights"></div>
<div class="abs tile photo" style="left:429px;top:1836px;background:linear-gradient(160deg,#e8d8b0,#e0a060 50%,#b8503a)" role="img" aria-label="Children at a birthday table with balloons"></div>
<div class="abs tile photo" style="left:607px;top:1836px;background:linear-gradient(160deg,#7a7a7a,#4a4a4a)" role="img" aria-label="Event guests gathered together"><div class="abs viewall">View All<i></i></div></div>
<div class="abs tile photo" style="left:785px;top:1836px;background:linear-gradient(160deg,#c08050,#7a3a22 55%,#2a1208)" role="img" aria-label="Friends clinking glasses"></div>
<div class="abs tile photo" style="left:251px;top:2013px;background:linear-gradient(160deg,#e8ecef,#b8c4cc 50%,#6a7480)" role="img" aria-label="Bride and groom embracing"></div>
<div class="abs tile photo" style="left:429px;top:2013px;background:linear-gradient(160deg,#c0603a,#3a3a5a 55%,#1a1a2a)" role="img" aria-label="Audience applauding at a corporate event"></div>
<div class="abs tile photo" style="left:607px;top:2013px;background:linear-gradient(160deg,#b0a8a0,#6a5a50 55%,#3a302a)" role="img" aria-label="Conference room with a presenter"></div>
<div class="abs tile photo" style="left:785px;top:2013px;background:linear-gradient(180deg,#cfe4ee,#e8d8e0 50%,#8aa070)" role="img" aria-label="Outdoor wedding arch with flowers"></div>

<!-- Testimonial -->
<section class="abs testi">
  <div class="abs avatar photo" role="img" aria-label="Portrait of a client"></div>
  <div class="abs stars"><svg width="66" height="11" viewBox="0 0 66 11"><g fill="#f2c200"><polygon points="5.5,0 7,4 11,4 8,6.5 9,11 5.5,8.5 2,11 3,6.5 0,4 4,4"/><polygon transform="translate(13.5 0)" points="5.5,0 7,4 11,4 8,6.5 9,11 5.5,8.5 2,11 3,6.5 0,4 4,4"/><polygon transform="translate(27 0)" points="5.5,0 7,4 11,4 8,6.5 9,11 5.5,8.5 2,11 3,6.5 0,4 4,4"/><polygon transform="translate(40.5 0)" points="5.5,0 7,4 11,4 8,6.5 9,11 5.5,8.5 2,11 3,6.5 0,4 4,4"/><polygon transform="translate(54 0)" points="5.5,0 7,4 11,4 8,6.5 9,11 5.5,8.5 2,11 3,6.5 0,4 4,4"/></g></svg></div>
  <p class="abs quote">Lorem Ipsum is simply dummy text of the printing and typesetting industry. Lorem Ipsum has been the industry's standard<br>dummy text ever since the 1500s, when an unknown printer took a galley of type and scrambled it to make a type s<br>survived not only five centuries, but also the leap into</p>
  <div class="abs author"><b>Evan Marlow</b> - 17/Nob/2016</div>
  <svg class="abs pager" viewBox="0 0 360 10"><line x1="0" y1="5" x2="168" y2="5" stroke="#777"/><line x1="192" y1="5" x2="360" y2="5" stroke="#777"/><circle cx="174" cy="5" r="4.5" fill="#f26a21"/><circle cx="186" cy="5" r="4.5" fill="#f26a21"/></svg>
</section>

<!-- Availability -->
<section class="abs avail">
  <div class="abs select" style="left:268px">Month<svg width="7" height="5"><polyline points="0,0 3.5,4 7,0" fill="none" stroke="#777"/></svg></div>
  <div class="abs select" style="left:438px">Day<svg width="7" height="5"><polyline points="0,0 3.5,4 7,0" fill="none" stroke="#777"/></svg></div>
  <div class="abs select" style="left:610px">Year<svg width="7" height="5"><polyline points="0,0 3.5,4 7,0" fill="none" stroke="#777"/></svg></div>
  <div class="abs check">Check Availability</div>
</section>

<!-- Footer -->
<div class="abs social"><i></i><i></i><i></i><i></i><i></i></div>
<div class="abs sec-rule" style="top:2624px;left:249px;width:702px"></div>
<div class="abs foot-col" style="left:249px"><h5>News &amp; Media</h5><ul><li>Latest Stories</li><li>Press Releases</li><li>Media Inquires</li><li>Media Partners</li><li>The News</li></ul></div>
<div class="abs foot-col" style="left:435px"><h5>Support</h5><ul><li>Latest Stories</li><li>Press Releases</li><li>Media Inquires</li><li>Media Partners</li><li>The News</li></ul></div>
<div class="abs foot-col" style="left:609px"><h5>Event</h5><ul><li>Latest Stories</li><li>Press Releases</li><li>Media Inquires</li><li>Media Partners</li><li>The News</li></ul></div>
<div class="abs foot-col" style="left:766px"><h5>News &amp; Media</h5><ul><li>Submit Your Story</li><li>Member Updates Archive</li><li>Contact</li><li>Login</li></ul></div>
<div class="abs sec-rule" style="top:2821px;left:249px;width:702px"></div>
<div class="abs copyright">© maplelanternco.example . 2017. All Rights reserved.  Privacy Policy</div>

</body>
</html>
```